Business card for law firm

Need business card for new law firm. Think confident, authoritative, conservative, but not stuffy or old-fashioned.

Contact Information for Business Card

Content for card - logo (uploaded), plus the following:

Paul Whitcombe (larger font)
Managing Partner (larger font, but not as large as name)
Level 9, 7 Ferris Lane
Sydney NSW 2000
Main Tel 02 9364 2710
Direct Tel 02 8472 3159
Email paul@qvlegal.com.au
www.qvlegal.com.au

Letterhead design should include logo plus:
Level 9, 7 Ferris Lane
Sydney NSW 2000
Tel 02 8472 3159
www.qvlegal.com.au

```html
<!DOCTYPE html>
<html lang="en">
<head>
<meta charset="utf-8">
<title>Quayvale Legal – Business Card</title>
<link href="https://fonts.googleapis.com/css2?family=EB+Garamond:wght@400;500&display=swap" rel="stylesheet">
<style>
  :root {
    --navy: #0c2a6e;
    --ink: #1a1a1a;
    --grey: #6b6b6b;
    --rule: #d9d9d9;
    --card: #ffffff;
    --stage: #e9e6e1;
  }
  * { box-sizing: border-box; margin: 0; padding: 0; }
  html, body { width: 1200px; height: 768px; overflow: hidden; }
  body {
    background: var(--stage);
    font-family: "EB Garamond", Georgia, serif;
    display: flex;
    align-items: center;
    justify-content: center;
    gap: 60px;
  }
  .card {
    width: 520px;
    height: 300px;
    background: var(--card);
    box-shadow: 0 6px 18px rgba(0,0,0,0.18);
    position: relative;
  }
  /* Front: contact side */
  .card-front { display: flex; }
  .front-mark {
    width: 250px;
    display: flex;
    align-items: center;
    justify-content: center;
  }
  .front-mark .firm-name {
    color: var(--navy);
    font-size: 40px;
    font-weight: 500;
    letter-spacing: 2px;
    line-height: 1.05;
    text-align: center;
  }
  .front-divider {
    width: 1px;
    margin: 34px 0;
    background: var(--rule);
  }
  .front-details {
    flex: 1;
    padding: 46px 0 0 30px;
  }
  .person-name {
    color: var(--navy);
    font-size: 25px;
    text-transform: uppercase;
    letter-spacing: 0.5px;
    line-height: 1;
  }
  .person-role {
    color: var(--ink);
    font-size: 17px;
    text-transform: uppercase;
    line-height: 1.2;
    margin-bottom: 14px;
  }
  .address, .contact-list {
    color: var(--grey);
    font-size: 15px;
    line-height: 1.35;
  }
  .address { margin-bottom: 8px; }
  .contact-list { list-style: none; }
  .contact-list li { display: flex; align-items: center; gap: 8px; }
  .contact-list svg { width: 11px; height: 11px; fill: var(--navy); flex: none; }
  /* Back: brand side */
  .card-back {
    display: flex;
    align-items: center;
    justify-content: center;
  }
  .brand { display: flex; align-items: center; gap: 16px; }
  .brand-square { width: 34px; height: 34px; background: var(--navy); }
  .brand-words { text-align: center; color: var(--ink); }
  .brand-name { font-size: 44px; letter-spacing: 3px; line-height: 1; }
  .brand-sub { font-size: 13px; letter-spacing: 14px; margin-top: 6px; padding-left: 14px; }
</style>
</head>
<body>
  <section class="card card-front">
    <div class="front-mark">
      <span class="firm-name">QUAYVALE<br>LEGAL</span>
    </div>
    <div class="front-divider"></div>
    <div class="front-details">
      <p class="person-name">Paul Whitcombe</p>
      <p class="person-role">Managing Partner</p>
      <p class="address">Level 9, 7 Ferris Lane<br>Sydney NSW 2000</p>
      <ul class="contact-list">
        <li><svg viewBox="0 0 24 24"><path d="M6.6 10.8a15.1 15.1 0 0 0 6.6 6.6l2.2-2.2a1 1 0 0 1 1-.25 11.4 11.4 0 0 0 3.6.57 1 1 0 0 1 1 1V20a1 1 0 0 1-1 1A17 17 0 0 1 3 4a1 1 0 0 1 1-1h3.5a1 1 0 0 1 1 1c0 1.25.2 2.45.57 3.57a1 1 0 0 1-.25 1z"/></svg>02 9364 2710</li>
        <li><svg viewBox="0 0 24 24"><path d="M6.6 10.8a15.1 15.1 0 0 0 6.6 6.6l2.2-2.2a1 1 0 0 1 1-.25 11.4 11.4 0 0 0 3.6.57 1 1 0 0 1 1 1V20a1 1 0 0 1-1 1A17 17 0 0 1 3 4a1 1 0 0 1 1-1h3.5a1 1 0 0 1 1 1c0 1.25.2 2.45.57 3.57a1 1 0 0 1-.25 1z"/></svg>02 8472 3159</li>
        <li><svg viewBox="0 0 24 24"><path d="M2 5h20v14H2z M2 5l10 8 10-8" fill="none" stroke="#0c2a6e" stroke-width="2.5"/></svg>paul@qvlegal.com.au</li>
        <li><svg viewBox="0 0 24 24"><circle cx="12" cy="12" r="10" fill="none" stroke="#0c2a6e" stroke-width="2.5"/><path d="M2 12h20M12 2c3 3 3 17 0 20M12 2c-3 3-3 17 0 20" fill="none" stroke="#0c2a6e" stroke-width="2"/></svg>www.qvlegal.com.au</li>
      </ul>
    </div>
  </section>

  <section class="card card-back">
    <div class="brand">
      <div class="brand-words">
        <p class="brand-name">QUAYVALE</p>
        <p class="brand-sub">LEGAL</p>
      </div>
      <span class="brand-square"></span>
    </div>
  </section>
</body>
</html>
```